UI/ UX Design for ERP Software

We need a new UX/UI interface for a ERP software for property managers. Our CMMS / ERP solution is made based on responsive design technologies and is coded in PHP.
The overall UX to be similar to Tev Ulna - easy navigation, intuitive menus.

Industry/Entity Type

Property Management

Number of Pages Required

5+ page

Requirements
Must have
• Round dock buttons
Consistent icons across the application
Enough Spacing between buttons/icons/ menu
Consistent Font
Nice to have
• We would like the UX to allow the users to use the application without /minimum training.
Should not have
• we don't want anything that is classic with respect to UX

```html
<!DOCTYPE html>
<html lang="en">
<head>
<meta charset="utf-8">
<title>Lotly — Active Dashboard</title>
<link href="https://fonts.googleapis.com/css2?family=Nunito+Sans:wght@400;600;700;800&display=swap" rel="stylesheet">
<style>
  :root{
    --bg:#f8f8f8;
    --panel:#ffffff;
    --ink:#1f2328;
    --muted:#5a6270;
    --line:#e6e8eb;
    --accent:#0db4f0;
    --brand:#1b6fd8;
    --button:#556275;
  }
  *{box-sizing:border-box;margin:0;padding:0}
  html,body{width:1200px;height:1059px;overflow:hidden}
  body{background:var(--bg);font-family:"Nunito Sans",sans-serif;color:var(--ink);position:relative}

  .sidebar{position:absolute;left:0;top:0;width:227px;height:1059px;background:var(--panel)}
  .brand{position:absolute;left:36px;top:38px;display:flex;align-items:center;gap:8px}
  .brand-square{width:22px;height:22px;background:var(--brand)}
  .brand-name{font-size:26px;font-weight:800;color:var(--brand);letter-spacing:.3px}
  .nav{position:absolute;left:21px;top:105px;width:182px;list-style:none}
  .nav li{height:38.8px;display:flex;align-items:center;gap:10px;padding-left:12px;font-size:11.3px;border-bottom:1px solid var(--line)}
  .nav li:last-child{border-bottom:none}
  .nav svg{width:11px;height:11px;fill:var(--muted);flex:none}

  .page-title{position:absolute;left:256px;top:42px;font-size:15px;font-weight:800;letter-spacing:.3px}
  .range-button{position:absolute;left:998px;top:40px;width:172px;height:32px;background:var(--button);color:#fff;font-size:10px;font-weight:700;display:flex;align-items:center;justify-content:space-between;padding:0 13px;letter-spacing:.3px}
  .range-button svg{width:10px;height:10px;stroke:#fff;fill:none;stroke-width:1.4}

  .stat{position:absolute;top:100px;width:175px;height:100px;background:var(--panel);border:1px solid #dcdfe3;text-align:center}
  .stat svg{display:block;margin:13px auto 0;width:26px;height:26px;stroke:var(--muted);fill:none;stroke-width:1.4}
  .stat-value{margin-top:5px;font-size:13.5px;font-weight:800;color:var(--accent)}
  .stat-label{margin-top:2px;font-size:10px;color:var(--ink);letter-spacing:.2px}

  .chart-panel{position:absolute;left:258px;top:234px;width:913px;height:428px;background:var(--panel)}
  .chart-panel svg{position:absolute;left:0;top:0}
  .axis{font-size:7.5px;fill:#444;font-family:"Nunito Sans",sans-serif}
  .legend{font-size:8.3px;fill:#333;font-family:"Nunito Sans",sans-serif}
</style>
</head>
<body>
<aside class="sidebar">
  <div class="brand"><span class="brand-square"></span><span class="brand-name">Lotly</span></div>
  <ul class="nav">
    <li><svg viewBox="0 0 12 12"><path d="M6 1 0 6h2v5h3V8h2v3h3V6h2z"/></svg>Dashboard</li>
    <li><svg viewBox="0 0 12 12"><circle cx="6" cy="3.5" r="2.2"/><circle cx="2" cy="4.5" r="1.5"/><circle cx="10" cy="4.5" r="1.5"/><path d="M2 11c0-3 8-3 8 0zM0 10c0-2 2-3 3-2.5L2 10zM12 10c0-2-2-3-3-2.5l1 2.5z"/></svg>Customers</li>
    <li><svg viewBox="0 0 12 12"><path d="M2 0h8v12H2zM3.5 2v1.5h1.5V2zm3.5 0v1.5h1.5V2zM3.5 5v1.5h1.5V5zm3.5 0v1.5h1.5V5zM3.5 8v1.5h1.5V8zm3.5 0v1.5h1.5V8z" fill-rule="evenodd"/></svg>Properties</li>
    <li><svg viewBox="0 0 12 12"><path d="M6 0 0 4v8h12V4zm0 4a1.5 1.5 0 1 1 0 3 1.5 1.5 0 0 1 0-3zM3 11c0-3 6-3 6 0z" fill-rule="evenodd"/></svg>Tenants</li>
    <li><svg viewBox="0 0 12 12"><path d="M0 2h12v1.5H0zm0 3.3h12v1.5H0zm0 3.3h12v1.5H0z"/></svg>Contacts</li>
    <li><svg viewBox="0 0 12 12"><path d="M0 5h3v7H0zm4 0 3-5c1.5 0 1.5 1.5 1 3h3.5c1 0 .5 1.5 0 2l-1.5 7H4z"/></svg>Contractors</li>
    <li><svg viewBox="0 0 12 12"><circle cx="6" cy="3" r="2.8"/><path d="M1 12c0-5 10-5 10 0z"/></svg>Employees</li>
    <li><svg viewBox="0 0 12 12"><path d="M0 2h6v1H1v8h8V7h1v5H0zM10 0l2 2-6 6H4V6z"/></svg>Compliance Managemem</li>
    <li><svg viewBox="0 0 12 12"><path d="M5 0h2l.3 1.6 1.4.6 1.4-.9 1.4 1.4-.9 1.4.6 1.4L12 5v2l-1.6.3-.6 1.4.9 1.4-1.4 1.4-1.4-.9-1.4.6L7 12H5l-.3-1.6-1.4-.6-1.4.9-1.4-1.4.9-1.4-.6-1.4L0 7V5l1.6-.3.6-1.4-.9-1.4 1.4-1.4 1.4.9 1.4-.6zm1 4a2 2 0 1 0 0 4 2 2 0 0 0 0-4z" fill-rule="evenodd"/></svg>Prevent. Maintenance</li>
    <li><svg viewBox="0 0 12 12"><path d="M4 1h4v2h4v9H0V3h4zm1 1v1h2V2zM0 6h12v1H0z" fill-rule="evenodd"/></svg>Work Orders</li>
    <li><svg viewBox="0 0 12 12"><path d="M0 1h2l.5 2H12l-1.5 5H3.5L2 2.5zM4 9.5a1 1 0 1 1 0 2 1 1 0 0 1 0-2zm5 0a1 1 0 1 1 0 2 1 1 0 0 1 0-2z"/></svg>Purchase Orders</li>
    <li><svg viewBox="0 0 12 12"><path d="M5 0a5 5 0 0 1 4 8l3 3-1 1-3-3A5 5 0 1 1 5 0zm0 1.8a3.2 3.2 0 1 0 0 6.4 3.2 3.2 0 0 0 0-6.4z" fill-rule="evenodd"/></svg>Property Inspections</li>
    <li><svg viewBox="0 0 12 12"><path d="M7 0 2 7h3.5L4 12l6-7.5H6.5z"/></svg>Energy Management</li>
    <li><svg viewBox="0 0 12 12"><path d="M6 0 11 2v4c0 3-2.5 5-5 6-2.5-1-5-3-5-6V2zm0 2v8c1.5-.8 3-2 3-4V3.3z" fill-rule="evenodd"/></svg>Risk Management</li>
    <li><svg viewBox="0 0 12 12"><circle cx="6" cy="3.5" r="2.5"/><path d="M0 9c2-1 3-1 5 0h3l4-2v2l-4 3H0z"/></svg>Project Management</li>
    <li><svg viewBox="0 0 12 12"><path d="M6 0a6 6 0 1 1 0 12A6 6 0 0 1 6 0zm0 1.3a4.7 4.7 0 1 0 0 9.4 4.7 4.7 0 0 0 0-9.4zM5.4 3h1.2v1H8v1.2H5.6v.6H8V9H6.6v1H5.4V9H4V7.8h2.4v-.6H4V4h1.4z" fill-rule="evenodd"/></svg>Financial - Budgeting</li>
    <li><svg viewBox="0 0 12 12"><path d="M0 8c2-3 5-5 9-5l3 2-4 2H4l-2 3z"/></svg>Tenant Requests</li>
    <li><svg viewBox="0 0 12 12"><path d="M1 0h6l4 4v8H1zm2 6v1h6V6zm0 2.5v1h6v-1z" fill-rule="evenodd"/></svg>Reports</li>
    <li><svg viewBox="0 0 12 12"><path d="M0 11h12v1H0zM1 6h2v5H1zm3-3h2v8H4zm3 2h2v6H7zm3-4h2v10h-2z"/></svg>Visual Reports</li>
    <li><svg viewBox="0 0 12 12"><path d="M1 0h6l4 4v8H1zm1.2 1.2v9.6h7.6V4.6H6.4V1.2zM6 5l2 2.2H6.7V10H5.3V7.2H4z" fill-rule="evenodd"/></svg>Files</li>
    <li><svg viewBox="0 0 12 12"><path d="M1 0h6l4 4v8H1zm2 5v1h6V5zm0 2.5v1h6v-1z" fill-rule="evenodd"/></svg>Pages</li>
    <li><svg viewBox="0 0 12 12"><path d="M1 2 2 1l4 4 4-4 1 1-4 4 4 4-1 1-4-4-4 4-1-1 4-4z"/></svg>Configurations</li>
    <li><svg viewBox="0 0 12 12"><path d="M5 0h2l.3 1.6 1.4.6 1.4-.9 1.4 1.4-.9 1.4.6 1.4L12 5v2l-1.6.3-.6 1.4.9 1.4-1.4 1.4-1.4-.9-1.4.6L7 12H5l-.3-1.6-1.4-.6-1.4.9-1.4-1.4.9-1.4-.6-1.4L0 7V5l1.6-.3.6-1.4-.9-1.4 1.4-1.4 1.4.9 1.4-.6zm1 4a2 2 0 1 0 0 4 2 2 0 0 0 0-4z" fill-rule="evenodd"/></svg>Settings</li>
  </ul>
</aside>

<h1 class="page-title">ACTIVE DASHBOARD</h1>
<div class="range-button">LAST 7 DAYS<svg viewBox="0 0 10 10"><rect x="1" y="2" width="8" height="7"/><path d="M1 4h8M3 1v2M7 1v2"/></svg></div>

<div class="stat" style="left:258px"><svg viewBox="0 0 26 26"><path d="M3 24V3h13v21M16 9h7v15M1 24h24M6 6h2v2H6zm5 0h2v2h-2zM6 11h2v2H6zm5 0h2v2h-2zM6 16h2v2H6zm5 0h2v2h-2zm8-4h2v2h-2zm0 5h2v2h-2z"/></svg><div class="stat-value">3</div><div class="stat-label">PROPERTIES</div></div>
<div class="stat" style="left:443px"><svg viewBox="0 0 26 26"><path d="M2 8 13 2l11 6zM3 10h20M5 12v9m4-9v9m4-9v9m4-9v9m4-9v9M2 23h22"/></svg><div class="stat-value">8</div><div class="stat-label">TENANTS</div></div>
<div class="stat" style="left:627px"><svg viewBox="0 0 26 26"><path d="M3 2v21h21M6 5h14v14H6zM6 10l5-5m-5 10 10-10M6 19 20 5m-9 14 9-9m-4 9 4-4"/></svg><div class="stat-value">422,00.00 SQFT</div><div class="stat-label">TOTAL PROPERITIES AREA</div></div>
<div class="stat" style="left:812px"><svg viewBox="0 0 26 26"><path d="M5 2h16v22H5zM8 6h5M8 10h10M8 13h10M8 16h10M8 19h6M16 5l1.5-1.5L19 5"/></svg><div class="stat-value">233,500.00 SQFT</div><div class="stat-label">RENTED AREA</div></div>
<div class="stat" style="left:996px"><svg viewBox="0 0 26 26"><circle cx="11" cy="11" r="8"/><circle cx="11" cy="9" r="2.5"/><path d="M6.5 15c2-3 7-3 9 0M17 17l6 6"/></svg><div class="stat-value">188,500 SQFT</div><div class="stat-label">VACANCIES AREA</div></div>

<section class="chart-panel" aria-label="Maintenance and inspection activity over the last 7 days">
  <svg width="913" height="428" viewBox="0 0 913 428">
    <g stroke="#e8e9eb" stroke-width="1">
      <line x1="39" y1="47" x2="874" y2="47"/>
      <line x1="39" y1="99" x2="874" y2="99"/>
      <line x1="39" y1="148" x2="874" y2="148"/>
      <line x1="39" y1="200" x2="874" y2="200"/>
      <line x1="39" y1="257" x2="874" y2="257"/>
      <line x1="39" y1="320" x2="874" y2="320" stroke="#d4d6d9" stroke-width="1.5"/>
    </g>
    <g class="axis" text-anchor="end">
      <text x="32" y="50">1.25</text>
      <text x="32" y="102">1</text>
      <text x="32" y="151">0.75</text>
      <text x="32" y="203">0.5</text>
      <text x="32" y="260">0.25</text>
      <text x="32" y="323">0</text>
    </g>
    <rect x="329" y="99" width="5" height="221" fill="var(--accent)"/>
    <g class="axis" text-anchor="middle">
      <text x="91" y="347">12/27/2020</text>
      <text x="212" y="347">12/28/2020</text>
      <text x="334" y="347">12/29/2020</text>
      <text x="455" y="347">12/30/2020</text>
      <text x="576" y="347">12/31/2020</text>
      <text x="697" y="347">01/01/2021</text>
      <text x="819" y="347">01/02/2021</text>
    </g>
    <g>
      <circle cx="58" cy="394" r="3.6" fill="#7ddc6f"/>
      <circle cx="196" cy="394" r="3.6" fill="#0db4f0"/>
      <circle cx="341" cy="394" r="3.6" fill="#f4a05a"/>
      <circle cx="464" cy="394" r="3.6" fill="#3b3f44"/>
      <circle cx="581" cy="394" r="3.6" fill="#7f83f0"/>
      <circle cx="711" cy="394" r="3.6" fill="#f0506e"/>
      <circle cx="846" cy="394" r="3.6" fill="#c45cf0"/>
    </g>
    <g class="legend" text-anchor="middle">
      <text x="58" y="415">Schedule Maintenance</text>
      <text x="196" y="415">Completed Schedule Maintenance</text>
      <text x="341" y="415">uture Schedule Maintenance</text>
      <text x="464" y="415">cheduled work orders</text>
      <text x="581" y="415">Completed work orders</text>
      <text x="705" y="415">Property Inspection in Progress</text>
      <text x="840" y="415">Complete property Inspections</text>
    </g>
  </svg>
</section>
</body>
</html>
```